Icons/images for company values

We have five company values, we have a new logo and a new look. I would like drawn images for each value that are in keeping with our look and feel.

Target Market(s)

internal/staff

Industry/Entity Type

media compliance

Requirements
Must have
• colours aligned with logo.

```html
<!DOCTYPE html>
<html lang="en">
<head>
<meta charset="utf-8">
<title>Values 2023</title>
<link href="https://fonts.googleapis.com/css2?family=Poppins:wght@300;400;800;900&family=Oswald:wght@200&display=swap" rel="stylesheet">
<style>
  :root {
    --page-bg: #c6c6c6;
    --paper: #ffffff;
    --brand-blue: #0d87cc;
    --deep-teal: #0e5f80;
    --ink: #2f2f2f;
    --icon-grey: #3a3a3a;
    --band-dark: #0b6a98;
    --band-mid: #1190d6;
    --band-aqua: #4fd0b0;
    --band-mint: #7ef29a;
    --band-lime: #b6e775;
    --v1-ring: #f5d84a; --v1-title: #c6a52a; --v1-num: #f4df4e;
    --v2-ring: #b6e66c; --v2-title: #98c14c; --v2-num: #b9ea70;
    --v3-ring: #0e5f80; --v3-title: #0d587b; --v3-num: #0e6589;
    --v4-ring: #27a6c8; --v4-title: #1f9fc9; --v4-num: #2ba6c6;
    --v5-ring: #0d79bf; --v5-title: #0d73b8; --v5-num: #0f76bd;
  }
  * { box-sizing: border-box; margin: 0; padding: 0; }
  html, body {
    width: 1200px; height: 1080px; overflow: hidden;
    background: var(--page-bg);
  }
  .stage { position: relative; width: 1200px; height: 1080px; }
  .poster {
    position: absolute; left: 0; top: 116px;
    width: 1713px; height: 1210px;
    transform: scale(0.7005); transform-origin: 0 0;
    background: var(--paper); overflow: hidden;
    font-family: 'Poppins', sans-serif;
  }
  .brand {
    position: absolute; left: 137px; top: 168px;
    font-family: 'Poppins', sans-serif; font-weight: 300;
    font-size: 52px; letter-spacing: 26px; line-height: 1;
    color: var(--brand-blue);
  }
  .divider {
    position: absolute; left: 403px; top: 95px;
    width: 2px; height: 215px; background: #e4e4e4;
  }
  .headline {
    position: absolute; left: 448px; top: 96px;
    display: flex; align-items: baseline; white-space: nowrap;
  }
  .headline .word {
    font-family: 'Poppins', sans-serif; font-weight: 900;
    font-size: 192px; line-height: 1; color: var(--brand-blue);
    letter-spacing: 2px;
  }
  .headline .year {
    font-family: 'Oswald', sans-serif; font-weight: 200;
    font-size: 178px; line-height: 1; color: var(--deep-teal);
    letter-spacing: 24px; margin-left: 40px;
  }
  .band {
    position: absolute; left: 0; top: 546px; width: 1713px; height: 664px;
    background: linear-gradient(28deg, var(--band-dark) 0%, var(--band-mid) 42%, var(--band-aqua) 66%, var(--band-mint) 84%, var(--band-lime) 100%);
  }
  .value {
    position: absolute; top: 378px; width: 275px; height: 648px;
    text-align: center;
  }
  .value .pill {
    position: absolute; left: 0; top: 168px; width: 275px; height: 480px;
    background: var(--paper); border-radius: 0 0 137.5px 137.5px;
  }
  .value .ring {
    position: absolute; left: 12px; top: 0; width: 250px; height: 250px;
    border-radius: 50%; background: var(--ring);
    box-shadow: 0 10px 18px rgba(0,0,0,0.18);
  }
  .value .ring::after {
    content: ""; position: absolute; inset: 22px; border-radius: 50%;
    background: var(--paper); box-shadow: inset 0 4px 10px rgba(0,0,0,0.12);
  }
  .value .icon {
    position: absolute; left: 82px; top: 70px; width: 110px; height: 110px; z-index: 1;
  }
  .value .title {
    position: absolute; left: 0; width: 275px; top: 283px;
    font-weight: 800; font-size: 23.5px; line-height: 25px;
    text-transform: uppercase; color: var(--title);
  }
  .value .body {
    position: absolute; left: 22px; width: 231px;
    font-weight: 400; font-size: 18.5px; line-height: 21.6px; color: var(--ink);
  }
  .value .number {
    position: absolute; left: 0; width: 275px; top: 574px;
    font-weight: 800; font-size: 156px; line-height: 1; color: var(--num);
    text-shadow: 0 4px 8px rgba(0,0,0,0.22);
  }
  .v1 { left: 127px; --ring: linear-gradient(160deg, #f6e05a, #efcc3a); --title: var(--v1-title); --num: var(--v1-num); }
  .v2 { left: 424px; --ring: linear-gradient(160deg, #c4ec7a, #9fdc5e); --title: var(--v2-title); --num: var(--v2-num); }
  .v3 { left: 722px; --ring: linear-gradient(160deg, #127399, #0b4e6c); --title: var(--v3-title); --num: var(--v3-num); }
  .v4 { left: 1019px; --ring: linear-gradient(160deg, #33b4d3, #1f93ba); --title: var(--v4-title); --num: var(--v4-num); }
  .v5 { left: 1317px; --ring: linear-gradient(160deg, #1287cf, #0b66a8); --title: var(--v5-title); --num: var(--v5-num); }
  .collab-art {
    border-radius: 50%;
    background: radial-gradient(circle at 50% 40%, #9fd65a 0%, #4a4a4a 75%);
    opacity: 0.85;
  }
</style>
</head>
<body>
<div class="stage">
  <main class="poster">
    <div class="brand">NORVA</div>
    <div class="divider"></div>
    <h1 class="headline"><span class="word">VALUES</span><span class="year">2023</span></h1>

    <div class="band"></div>

    <section class="value v1">
      <div class="pill"></div>
      <div class="ring"></div>
      <svg class="icon" viewBox="0 0 100 100" aria-hidden="true">
        <path d="M50 48 C30 34 30 14 42 14 C47 14 50 19 50 22 C50 19 53 14 58 14 C70 14 70 34 50 48Z" fill="#bfa332"/>
        <path d="M6 30 L12 30 L14 56 L34 74 L34 96 L20 96 L20 80 L6 64Z" fill="var(--icon-grey)"/>
        <path d="M94 30 L88 30 L86 56 L66 74 L66 96 L80 96 L80 80 L94 64Z" fill="var(--icon-grey)"/>
        <path d="M18 52 L30 48 L42 62 L40 72Z M82 52 L70 48 L58 62 L60 72Z" fill="var(--icon-grey)"/>
      </svg>
      <h2 class="title">We're open<br>&amp; honest</h2>
      <p class="body" style="top:366px">Sharing information helps us achieve the best outcomes for our teams and business. We value open, honest, and clear communication.</p>
      <div class="number">1</div>
    </section>

    <section class="value v2">
      <div class="pill"></div>
      <div class="ring"></div>
      <div class="icon collab-art" role="img" aria-label="Two team members giving a high five"></div>
      <h2 class="title">We get there<br>faster,<br>together</h2>
      <p class="body" style="top:384px">Collaboration is at the heart of what we do, no matter our team.</p>
      <div class="number">2</div>
    </section>

    <section class="value v3">
      <div class="pill"></div>
      <div class="ring"></div>
      <svg class="icon" viewBox="0 0 100 100" aria-hidden="true">
        <path d="M50 4 C28 4 16 20 16 36 C16 50 26 58 30 66 L30 72 L70 72 L70 66 C74 58 84 50 84 36 C84 20 72 4 50 4Z" fill="var(--icon-grey)"/>
        <rect x="32" y="76" width="36" height="5" rx="2" fill="var(--icon-grey)"/>
        <rect x="34" y="84" width="32" height="5" rx="2" fill="var(--icon-grey)"/>
        <path d="M42 92 L58 92 L54 98 L46 98Z" fill="var(--icon-grey)"/>
        <path d="M50 16 L68 22 L68 36 C68 48 58 56 50 60 C42 56 32 48 32 36 L32 22Z" fill="#ffffff"/>
        <path d="M50 22 L63 26 L63 37 C63 45 56 51 50 54 C44 51 37 45 37 37 L37 26Z" fill="#1590c4"/>
      </svg>
      <h2 class="title">We are leaders<br>in copyright<br>&amp; intellectual<br>property</h2>
      <p class="body" style="top:398px">Leading the conversation in audio-visual copyright compliance and advocating for the protection of intellectual property globally.</p>
      <div class="number">3</div>
    </section>

    <section class="value v4">
      <div class="pill"></div>
      <div class="ring"></div>
      <svg class="icon" viewBox="0 0 100 100" aria-hidden="true">
        <rect x="2" y="12" width="80" height="64" rx="8" fill="var(--icon-grey)"/>
        <path d="M10 28 L42 46 L74 28" fill="none" stroke="#ffffff" stroke-width="7" stroke-linejoin="round"/>
        <circle cx="74" cy="72" r="22" fill="#ffffff"/>
        <path d="M74 52 L80 57 L88 56 L89 64 L95 70 L90 77 L91 85 L83 86 L78 92 L72 88 L64 90 L62 82 L55 77 L59 70 L57 62 L65 60 L68 53Z" fill="#27a6c8"/>
        <path d="M66 72 L72 78 L83 66" fill="none" stroke="#ffffff" stroke-width="4.5" stroke-linecap="round" stroke-linejoin="round"/>
      </svg>
      <h2 class="title">We get<br>things done</h2>
      <p class="body" style="top:356px">We grow through capability, focus and hard work. We believe small steps compound to big results.</p>
      <div class="number">4</div>
    </section>

    <section class="value v5">
      <div class="pill"></div>
      <div class="ring"></div>
      <svg class="icon" viewBox="0 0 100 100" aria-hidden="true">
        <rect x="20" y="14" width="60" height="82" rx="5" fill="var(--icon-grey)"/>
        <rect x="38" y="8" width="24" height="12" rx="3" fill="#0d79bf"/>
        <circle cx="50" cy="6" r="5" fill="#0d79bf"/>
        <path d="M35 56 L46 67 L66 45" fill="none" stroke="#ffffff" stroke-width="8" stroke-linecap="round" stroke-linejoin="round"/>
      </svg>
      <h2 class="title">Diverse<br>perspectives<br>build better<br>outcomes</h2>
      <p class="body" style="top:407px">We value diversity, inclusion, respect and trust within our teams. We are building a truly global organisation.</p>
      <div class="number">5</div>
    </section>
  </main>
</div>
</body>
</html>
```